Corporate website design needed

We need a Contemporary Industrial/Tech/Logistics Website design to match our logistic client's business. Our client consults and build logistics solutions that they manage but they are not a typical 3PL (3rd party logistics company) which is primarily engaged in moving boxes.
PSD file only for now, home and default templates.
COMPANY CHARACTER
DESIGN LOOK AND FEEL
• The design should also be modern and visually well organized — employing a combination of visual devices and info graphics. Keep it light and not too heavy but strong/ professional. And unique.
• The design should go beyond the typical industrial pick and pack 3PL representing [Logistics Company] as a High Tech/IT logistics company.
Some examples although these are not right for this client because they have much more content and present themselves more as a 3pl.
http://www.vobrelink-hub.example/ (More right then wrong - Like this but simplified)
http://www.durmaxfreight.example (Ugly)
http://www.tpwallerton.example (More right then wrong but different focus)
http://www.pelhamrye.example/ Too 3PL trucking… We want a bit ore high level approach
The difference, the design should be a fusion in core concepts that culminate in a design which implies the following attributes. Tech (Big data / analytics / software), Consultancy (Solutions, SME, Leader), 3PL Industry vertical solutions.
NOTE: The visualization of “tech” is not “1” and “0”, but more “software and analytics” Perhaps more like www.navimetra.example.
• They need to be seen as a solutions provider in Logistics and as in Subject matter experts
TONE
The tone needs to exude professionalism, expertise, though leadership along with technical and executional excellence.
Experienced
Knowledgeable
Confident
Determined
Straightforward
WEBSITE OBJECTIVES
• Focus C-Suite executives and logistics managers’ attention on [Logistics Company]s commanding knowledge and expertise, and unique approach to supply chain solutions producing more RFP wins
• Create an easy to scan design which decreases the reliance on text through featured text, summaries, and smaller “chunked” size bits of information.
• Convey [Logistics Company] as high-tech 3PL solutions developer and services provider with a ‘high-touch’ consultative approach.
• Showcase [Logistics Company]’s value propositions. (See Slider Content)
• Showcase [Logistics Company]’s expertise in logistical analytics.
• Gain recognition as an industry leader in evolutionary new space (supply chain 2.0)
WEBSITE STRATEGY
• Reduce reliance on text (at least within initial entry points for each section)
• Typography: Watch text line lengths and readability, bolder fonts. NO SERIFS
• Generally, create a click-through format so that users who want more details can find it, and those who don’t can get a snapshot without clicking through.
• Increase visual content through info graphics and some dynamic content, photography
• Better utilize the space on each page (e.g., add visual interest, photography and iconography where appropriate to break up copy blocks and maintain readable line lengths).
COLOR SCHEME
• Create a more engaging color scheme (the logo will remain the same under all circumstances).
• Red / grayscale may work…. Not too dark or heavy. Not too much red. Ex. quiltora.example
• Also try blues and greys. They seem to like that. Open to suggestions but don’t get to crazy. Red is in their logo but too much may be a problem.
PHOTOGRAPHY
Yes. And I will upload some.
If you pick photography please be sure to note Which stock house used and the image number!
CONTENT
The content will be presented in a more hierarchical format — with lead-ins, paragraph and section headers and navigational cues to expand lengthier content allowing the visitor to more easily scan the website. No case studies, No Social media, News while on the home page should not be over emphasized. They don't post a lot so it gets dated quickly ...
I will be uploading a wire frame and other elements.
NOTE: I uploaded my EXAMPLE mock up which is close but not close enough.
I am not a great designer. So I am looking for an alternative that exceed my design ability! These examples show the basic layout but I really want some varied alternatives.
The colors are inconsistent and type not quite right. The grey bar at top is not right and should probably go away.
Please pull the basic elements in the example together into a great design.
If you have questions please contact me.
i will upload some photography tomorrow that may be of use.
Thanks!
Updates
Hi All,
We are still evaluating the submitted designs. Sorry for the delay.
Target Market(s)
This website is primarily a validation website. Few new customers will search and find them as such...
The site should be Focused on C-Suite executives and logistics managers’ attention on [Logistics Company]s commanding knowledge and expertise, and unique approach to supply chain solutions producing more RFP wins
Industry/Entity Type
Business
Font styles to use
Requirements
Must have
- Slide show, Clearly explain who they are and what they do.
Create an easy to scan design which decreases the reliance on text through featured text, summaries, and smaller “chunked” size bits of information.
Convey [Logistics Company] as high-tech 3PL solutions developer and services
provider with a ‘high-touch’ consultative approach.
Should not have
- No Ads space
No Social media
Not too cluttered. Keep it clean.

```html
<!DOCTYPE html>
<html lang="en">
<head>
<meta charset="utf-8">
<title>Novaline Logistics — Home</title>
<link href="https://fonts.googleapis.com/css2?family=Open+Sans:wght@400;600;700&display=swap" rel="stylesheet">
<style>
:root{
  --red:#b0102a;
  --ink:#222;
  --text:#555;
  --line:#ddd;
  --charcoal:#3a3a3a;
  --footer:#2e2e2e;
  --footer-deep:#222;
  --blue:#1f5fa8;
  --white:#fff;
}
*{box-sizing:border-box;margin:0;padding:0}
html,body{width:744px;height:1200px;overflow:hidden;background:var(--white)}
body{font-family:"Open Sans",Arial,sans-serif;color:var(--text);font-size:9px;line-height:1.45}
.page{width:744px;height:1200px;display:flex;flex-direction:column}

/* header */
.site-header{position:relative;height:44px;flex:none;background:var(--white)}
.brand-name{position:absolute;left:22px;top:13px;font-weight:600;font-size:14px;color:var(--ink)}
.utility-bar{position:absolute;right:0;top:0;height:14px;width:330px;background:var(--charcoal);display:flex;align-items:center;justify-content:flex-end;gap:10px;padding-right:14px}
.utility-bar a{color:#ddd;text-decoration:none;font-size:7.5px}
.main-nav{position:absolute;right:18px;top:21px;display:flex;gap:22px}
.main-nav a{color:var(--ink);font-weight:700;font-size:10px;text-decoration:none}
.main-nav a::before{content:"▸ ";color:var(--red)}

/* hero */
.hero{position:relative;height:300px;flex:none;overflow:hidden}
.hero-photo{position:absolute;inset:0;background:linear-gradient(120deg,#0c2d5c 0%,#1d5aa0 40%,#5ea0de 70%,#1a3f78 100%)}
.hero-copy{position:absolute;left:40px;top:80px;width:310px;color:var(--white)}
.hero-copy h1{font-size:27px;font-weight:700;line-height:1.1}
.hero-copy .lead{font-size:12px;margin:4px 0 10px}
.hero-copy p{font-size:8px;color:#e3ecf7}
.slide-dots{position:absolute;right:40px;top:140px;display:flex;flex-direction:column;gap:6px}
.slide-dots span{width:7px;height:7px;border-radius:50%;background:rgba(255,255,255,.5)}
.slide-dots span.active{background:var(--white)}

/* intro band */
.intro-band{height:60px;flex:none;background:var(--charcoal);color:#ddd;font-size:8px;padding:14px 22px;line-height:1.8}

/* services */
.services{height:150px;flex:none;display:flex;justify-content:center;gap:30px;padding-top:28px}
.service{width:90px;text-align:center;font-size:8px;color:var(--ink);font-weight:600;line-height:1.3}
.service-icon{width:46px;height:46px;margin:0 auto 8px;background:var(--blue);border-radius:4px;display:flex;align-items:center;justify-content:center}

/* difference band */
.difference{height:170px;flex:none;background:var(--red);display:flex;gap:22px;padding:22px;color:var(--white)}
.diff-card{flex:1;display:flex;gap:12px}
.diff-photo{width:140px;height:126px;flex:none;background:linear-gradient(135deg,#c9c9c9,#8a8a8a)}
.diff-card h3{font-size:11px;font-weight:700;margin-bottom:3px}
.diff-card p{font-size:7.5px;color:#f6d8dc}

/* news & featured */
.news-row{height:290px;flex:none;display:flex;gap:24px;padding:20px 22px}
.col{flex:1}
.col h2{font-size:15px;font-weight:600;color:var(--red);border-bottom:1px solid var(--line);padding-bottom:4px;margin-bottom:10px}
.news-item{margin-bottom:14px}
.news-item p{font-size:7.5px}
.btn{display:inline-block;margin-top:5px;background:var(--charcoal);color:var(--white);font-size:7px;padding:3px 8px;text-decoration:none}
.more-link{color:var(--red);font-size:7.5px;font-weight:600;text-decoration:none}
.featured{display:flex;gap:10px}
.featured-photo{width:130px;height:80px;flex:none;background:linear-gradient(135deg,#8fa7bf,#4d6680)}
.featured p{font-size:7.5px}
.address{display:flex;gap:18px;margin-top:10px;font-size:7px}
.sales{margin-top:8px;font-size:12px;color:var(--red);font-weight:700;line-height:1.3}
.sales small{display:block;color:var(--text);font-size:8px;font-weight:400}

/* footer */
.site-footer{position:relative;height:146px;flex:none;background:var(--footer);padding:16px 30px;display:flex;gap:30px}
.footer-col{width:140px}
.footer-col h4{color:var(--white);font-size:11px;font-weight:700;margin-bottom:4px}
.footer-col li{list-style:none;color:#b5b5b5;font-size:7.5px;line-height:1.6}
.footer-brand{position:absolute;right:30px;bottom:16px;font-weight:600;font-size:14px;color:var(--white)}
.copyright{height:40px;flex:none;background:var(--footer-deep);color:#999;font-size:7px;text-align:center;padding-top:15px}
</style>
</head>
<body>
<div class="page">
  <header class="site-header">
    <span class="brand-name">Novaline Logistics</span>
    <nav class="utility-bar">
      <a href="#">Company</a><a href="#">Careers</a><a href="#">Contact</a><a href="#">Search</a><a href="#">Sales: 800-555-0142</a>
    </nav>
    <nav class="main-nav">
      <a href="#">Solutions</a><a href="#">Our Process</a><a href="#">Industries</a>
    </nav>
  </header>

  <section class="hero">
    <div class="hero-photo" role="img" aria-label="Businessman in a suit seen from behind facing a blue digital network backdrop"></div>
    <div class="hero-copy">
      <h1>A New Way To Think</h1>
      <div class="lead">about supply chain transformation</div>
      <p>Leading with data-driven insight, we shape supply chains that adapt and grow. Our team pairs analytics with hands-on execution to move your business forward with confidence.</p>
    </div>
    <div class="slide-dots"><span class="active"></span><span></span><span></span><span></span></div>
  </section>

  <div class="intro-band">Novaline manages complexity, provides data-driven solutions and implements innovative and actionable strategies that deliver business results.<br>Novaline manages complexity, provides data-driven solutions and implements innovative and actionable strategies.</div>

  <section class="services">
    <div class="service"><div class="service-icon"><svg width="26" height="26" viewBox="0 0 26 26" fill="none" stroke="#fff" stroke-width="2"><rect x="3" y="9" width="20" height="14"/><path d="M3 9l5-6h10l5 6"/></svg></div>Material Management &amp; Factory Support</div>
    <div class="service"><div class="service-icon"><svg width="26" height="26" viewBox="0 0 26 26" fill="none" stroke="#fff" stroke-width="2"><path d="M3 5h4l3 12h11l2-8H9"/><circle cx="11" cy="21" r="2"/><circle cx="19" cy="21" r="2"/></svg></div>Retail and e-Commerce Distribution</div>
    <div class="service"><div class="service-icon"><svg width="26" height="26" viewBox="0 0 26 26" fill="none" stroke="#fff" stroke-width="2"><circle cx="13" cy="13" r="8"/><circle cx="13" cy="13" r="3"/></svg></div>Aftermarket Support</div>
    <div class="service"><div class="service-icon"><svg width="26" height="26" viewBox="0 0 26 26" fill="none" stroke="#fff" stroke-width="2"><path d="M13 3l10 18H3z"/><path d="M13 10v5M13 18v1"/></svg></div>Critical Logistics</div>
    <div class="service"><div class="service-icon"><svg width="26" height="26" viewBox="0 0 26 26" fill="none" stroke="#fff" stroke-width="2"><path d="M4 8h15l-4-4M22 18H7l4 4"/></svg></div>Supply Chain Transformation Services</div>
  </section>

  <section class="difference">
    <div class="diff-card">
      <div class="diff-photo" role="img" aria-label="Business professional at work"></div>
      <div><h3>The Novaline Difference</h3><p>We commit our own capital and resources to align with our clients' goals. Unlike consultants, we implement and operate the solutions we design. We guarantee business performance for our clients, investing in and sharing the risks.</p></div>
    </div>
    <div class="diff-card">
      <div class="diff-photo" role="img" aria-label="Team meeting in an office"></div>
      <div><h3>The Novaline Difference</h3><p>Corporate profile</p></div>
    </div>
  </section>

  <section class="news-row">
    <div class="col">
      <h2>Recent News</h2>
      <div class="news-item"><p>Novaline Logistics named a top 3PL partner in operations by a regional industry council. Novaline Logistics, Inc. headquartered in Lindale Park, shares the award with its team.</p><a class="btn" href="#">Read more</a></div>
      <div class="news-item"><p>Novaline Logistics to invest in a new regional campus, adding jobs and modern distribution space to support growing retail and e-commerce clients.</p><a class="btn" href="#">Read more</a></div>
      <a class="more-link" href="#">More Novaline News ›</a>
    </div>
    <div class="col">
      <h2>Featured Industry</h2>
      <div class="featured">
        <div class="featured-photo" role="img" aria-label="Modern distribution warehouse exterior"></div>
        <p>Our modern 3PL network and logistics systems allow retailers and e-commerce companies to leverage our national footprint to provide support and customer service.</p>
      </div>
      <a class="btn" href="#">Read more</a>
      <div class="address"><span>Novaline Logistics<br>480 Harbor Crest Way<br>Lindale Park, 00000<br>800-555-0199</span><span>General Contact Form<br>Media Contact</span></div>
      <div class="sales">Sales Inquiries:<small>800-555-0142</small></div>
    </div>
  </section>

  <footer class="site-footer">
    <div class="footer-col"><h4>Our Process</h4><ul><li>Concept of operations</li><li>Engaging the infrastructure</li><li>Industry leading team</li><li>Managed services</li><li>Providing actionable strategies</li><li>Investing in our clients' success</li><li>Driving business results</li></ul></div>
    <div class="footer-col"><h4>Our Solutions</h4><ul><li>Business Analytics</li><li>Geographic Coverage</li><li>Project Planning</li><li>Project Implementation</li><li>Technology</li><li>Quality</li></ul></div>
    <div class="footer-col"><h4>Industries We Serve</h4><ul><li>Aerospace</li><li>Defense</li><li>Industrial</li><li>Manufacturing</li><li>Media and Entertainment</li><li>Medical</li><li>Retail</li><li>Telecom &amp; Electronics</li></ul></div>
    <div class="footer-col"><h4>Company</h4><ul><li>Culture</li><li>Community Involvement</li><li>Major Metro Presence</li><li>News</li><li>Careers</li><li>Contact</li></ul></div>
    <span class="footer-brand">Novaline Logistics</span>
  </footer>
  <div class="copyright">© 2014 Novaline. All Rights Reserved.</div>
</div>
</body>
</html>
```